Brightfen Business Card Redesign & Logo Update

We need to update our business cards to something more modern and fresh. Brightfen can provide the current color schemes and old design examples, but welcome creativity in helping us with this redesign. PLEASE NOTE that we no longer utilize the "tree" and/or "leaf" imagery in our branding. If able would apprecaite an update on the quality of our "words only" logo in Ai. / PNG formats too.

Target Market(s)

Investors, landowners, corporate partners, contractors

Industry/Entity Type

Environmental Restoration & Conservation

Contact Information for Business Card

Logo, persons name, title, mailing address, phone and email, website url

Font styles to use
Other font styles liked:
• Merriweather

Requirements
Nice to have
• Logo, persons name, title, mailing address, phone and email, website url, but open to ideams
Should not have
• No all back backgrounds

```html
<!DOCTYPE html>
<html lang="en">
<head>
<meta charset="UTF-8">
<title>Brightfen Business Card</title>
<link rel="stylesheet" href="https://fonts.googleapis.com/css2?family=Open+Sans:wght@400;600;700&display=swap">
<style>
  :root {
    --stage: #2b2b2e;
    --card-dark: #212125;
    --orange: #ee7f24;
    --orange-deep: #d56c14;
    --green: #14843d;
    --white: #ffffff;
    --body-font: "Open Sans", sans-serif;
  }
  * { box-sizing: border-box; margin: 0; padding: 0; }
  html, body { width: 1200px; height: 780px; overflow: hidden; }
  body {
    background: var(--stage);
    position: relative;
    font-family: var(--body-font);
  }
  .card {
    position: absolute;
    top: 60px;
    width: 380px;
    height: 660px;
    overflow: hidden;
  }

  /* Back of card */
  .card-back {
    left: 170px;
    background: var(--orange);
    border-radius: 160px 160px 0 0;
  }
  .back-mark {
    position: absolute;
    left: 50%;
    top: 54%;
    transform: translate(-50%, -50%) rotate(-90deg);
    color: var(--orange-deep);
    white-space: nowrap;
    font-weight: 700;
  }
  .back-name {
    font-size: 100px;
    line-height: 1.05;
  }
  .back-tagline {
    font-size: 28px;
    line-height: 1.2;
    padding-left: 6px;
  }

  /* Front of card */
  .card-front {
    left: 650px;
    background: var(--card-dark);
    border: 4px solid var(--orange);
    border-radius: 0 0 160px 160px;
  }
  .front-logo {
    position: absolute;
    left: 34px;
    top: 40px;
  }
  .brand-name {
    font-weight: 700;
    font-size: 58px;
    line-height: 1.1;
    color: var(--orange);
  }
  .brand-tagline {
    font-weight: 600;
    font-size: 15px;
    color: var(--white);
    margin-top: 2px;
    padding-left: 3px;
  }
  .contact-block {
    position: absolute;
    left: 0;
    right: 0;
    top: 380px;
    text-align: center;
    color: var(--white);
  }
  .person-name {
    font-weight: 700;
    font-size: 28px;
    letter-spacing: 0.5px;
  }
  .person-title {
    font-size: 17px;
    margin-top: 2px;
  }
  .icon-row {
    display: flex;
    align-items: center;
    justify-content: center;
    gap: 12px;
    margin: 18px 0 14px;
  }
  .divider {
    width: 88px;
    height: 2px;
    background: var(--green);
  }
  .icon {
    width: 28px;
    height: 28px;
  }
  .contact-lines {
    font-size: 15px;
    line-height: 1.55;
  }
</style>
</head>
<body>

  <section class="card card-back" aria-label="Card back">
    <div class="back-mark">
      <div class="back-name">Brightfen</div>
      <div class="back-tagline">Land Restoration Group</div>
    </div>
  </section>

  <section class="card card-front" aria-label="Card front">
    <div class="front-logo">
      <div class="brand-name">Brightfen</div>
      <div class="brand-tagline">Land Restoration Group</div>
    </div>

    <div class="contact-block">
      <div class="person-name">Marta Kovanda</div>
      <div class="person-title">Founder</div>

      <div class="icon-row">
        <span class="divider"></span>
        <svg class="icon" viewBox="0 0 28 28" aria-label="Phone">
          <circle cx="14" cy="14" r="12.5" fill="none" stroke="var(--green)" stroke-width="2.5"/>
          <path d="M10 8.5c-1 .6-1.6 1.6-1.2 3 .9 3 3.3 5.5 6.3 6.5 1.3.4 2.4-.2 3-1.2l-2.2-1.8-1.3 1c-1.5-.7-2.6-1.8-3.3-3.3l1-1.3z" fill="var(--orange)"/>
        </svg>
        <svg class="icon" viewBox="0 0 28 28" aria-label="Email">
          <circle cx="14" cy="14" r="12.5" fill="none" stroke="var(--green)" stroke-width="2.5"/>
          <rect x="8" y="10" width="12" height="8.5" rx="1" fill="var(--orange)"/>
          <path d="M8.5 10.5 14 15l5.5-4.5" fill="none" stroke="var(--card-dark)" stroke-width="1.2"/>
        </svg>
        <svg class="icon" viewBox="0 0 28 28" aria-label="Website">
          <circle cx="14" cy="14" r="12.5" fill="none" stroke="var(--green)" stroke-width="2.5"/>
          <circle cx="14" cy="14" r="6.5" fill="none" stroke="var(--orange)" stroke-width="1.6"/>
          <ellipse cx="14" cy="14" rx="2.8" ry="6.5" fill="none" stroke="var(--orange)" stroke-width="1.3"/>
          <line x1="7.5" y1="14" x2="20.5" y2="14" stroke="var(--orange)" stroke-width="1.3"/>
        </svg>
        <span class="divider"></span>
      </div>

      <div class="contact-lines">
        <div>(555) 014-6310</div>
        <div>hello@brightfen.com</div>
        <div>www.brightfen.com</div>
      </div>
    </div>
  </section>

</body>
</html>
```